Website for a Steadwell, an HVAC company.

We are a company that provides residential and commercial service. We don’t need any widgets other than a call to action where customers can message us. Though we have very few google reviews, they are all great and would like to see those populated. Simple and modern is the style. I included our logo and a pic of our vans.

Target Market(s)

Residential customers

Coding

Coded - Design and coding required

Number of Pages Required

1 page

Font styles to use
Sans Serif

Colors
0054AA
0677BA
7BADD7
CADEEF
E8F1F8
EE7325
F08F49
F5BC92
FAE3D3
FDF4ED

```html
<!DOCTYPE html>
<html lang="en">
<head>
<meta charset="utf-8">
<title>Steadwell Heating and Air — Home Page Layouts</title>
<link href="https://fonts.googleapis.com/css2?family=Poppins:wght@300;400;500;600;700;800&family=Roboto:wght@300;400;500;700&display=swap" rel="stylesheet">
<style>
:root{
  --board:#a6a6a6;
  --ink:#111111;
  --black:#000000;
  --white:#ffffff;
  --admin:#1d2327;
  --orange:#ee7325;
  --orange-soft:#f08f49;
  --red:#c8341f;
  --yellow:#ffc20e;
  --blue-btn:#2f5bf0;
  --blue-cta:#1b8ad0;
  --navy:#0b2a4a;
  --slate:#7f94a8;
  --muted:#666666;
  --line:#d9dde2;
  --social:#ef2147;
  --nav-active:#2ecc71;
}
*{box-sizing:border-box;margin:0;padding:0}
html,body{width:1200px;height:2811px;overflow:hidden}
body{background:var(--board);font-family:"Roboto",sans-serif;color:var(--ink);position:relative}
.board-title{position:absolute;left:0;width:1240px;top:40px;text-align:center;font-family:"Poppins",sans-serif;font-weight:500;font-size:40px;letter-spacing:.5px;color:var(--ink)}
.view-label{position:absolute;top:140px;font-family:"Poppins",sans-serif;font-weight:500;font-size:46px;color:var(--ink)}
.frame{position:absolute;background:var(--white);overflow:hidden}
.frame--desktop{left:77px;top:227px;width:600px;height:2505px}
.frame--mobile{left:785px;top:227px;width:345px;height:2363px}
.abs{position:absolute}
.center{left:0;right:0;text-align:center}
.admin-bar{position:absolute;left:0;top:0;right:0;background:var(--admin);color:#c3c4c7;font-size:6px;display:flex;align-items:center;padding:0 8px;gap:9px}
.admin-bar .spacer{flex:1}
.dot{display:inline-block;width:6px;height:6px;border-radius:50%;background:#8c8f94;vertical-align:middle;margin-right:2px}
.site-header{position:absolute;left:0;right:0;background:var(--black)}
.brand{position:absolute;display:flex;flex-direction:column;align-items:center;gap:3px;font-family:"Poppins",sans-serif;font-weight:700;color:var(--orange);letter-spacing:1.5px;text-transform:uppercase}
.brand .mark{border-radius:50%;background:var(--orange)}
.nav{position:absolute;display:flex;gap:20px;font-family:"Poppins",sans-serif;font-size:8px;color:#cfcfcf}
.nav .active{color:var(--nav-active);position:relative}
.nav .active::after{content:"";position:absolute;left:-8px;right:-8px;bottom:-6px;height:1px;background:var(--nav-active)}
.hero-bg{position:absolute;left:0;right:0;background:var(--black)}
.photo-hero{position:absolute;left:0;right:0;background:linear-gradient(160deg,#6d6f70 0%,#3a3d44 35%,#10182e 60%,#1c2a55 75%,#5a5a56 100%)}
.social-rail{position:absolute;left:0;background:var(--social);display:flex;flex-direction:column;align-items:center;justify-content:space-evenly}
.social-rail span{border-radius:50%;background:var(--white)}
.hero-kicker{font-family:"Roboto",sans-serif;font-weight:300;color:var(--white)}
.hero-title{font-family:"Poppins",sans-serif;font-weight:800;color:var(--yellow);text-transform:uppercase;line-height:1.05}
.btn{position:absolute;display:flex;align-items:center;justify-content:center;border-radius:999px;font-family:"Poppins",sans-serif;color:var(--white)}
.btn--quote{background:var(--blue-btn);font-weight:700;text-transform:uppercase}
.btn--book{background:var(--orange);font-weight:400}
.btn--cta{background:var(--blue-cta);border-radius:2px;font-weight:500}
.section-title{font-family:"Poppins",sans-serif;font-weight:600;color:var(--orange)}
.lead{font-family:"Roboto",sans-serif;font-weight:300;color:#444}
.lead b{font-weight:700;color:var(--navy)}
.service-photo{position:absolute;border-radius:6px;background:linear-gradient(135deg,#c9cbcd,#8d8f92 55%,#e6e6e4)}
.service-photo.alt{background:linear-gradient(135deg,#dcdcd8,#f2f2f0 45%,#5f7ea8)}
.service-photo.warm{background:linear-gradient(135deg,#e3e2dc,#9a8f80 45%,#3c4a66)}
.service-name{position:absolute;text-align:center;font-family:"Poppins",sans-serif;font-weight:600;color:var(--red)}
.service-text{position:absolute;text-align:center;font-family:"Roboto",sans-serif;font-weight:300;color:#555;line-height:1.35}
.band-dark{position:absolute;left:0;right:0;background:var(--black)}
.why-title{font-family:"Poppins",sans-serif;font-weight:600;color:var(--orange)}
.why-caps{font-family:"Roboto",sans-serif;font-weight:500;color:var(--white);text-transform:uppercase;line-height:1.3}
.feature{position:absolute;text-align:center}
.feature svg{display:block;margin:0 auto}
.feature h3{font-family:"Poppins",sans-serif;font-weight:600;color:var(--orange);line-height:1.1}
.feature p{font-family:"Roboto",sans-serif;font-weight:300;color:var(--white);line-height:1.35}
.partners{position:absolute;left:0;right:0;background:linear-gradient(#ffffff,#f3f4f5)}
.partners-label{font-family:"Roboto",sans-serif;font-weight:300;color:#4a5a6a}
.badge{position:absolute}
.contact{position:absolute;left:0;right:0;background:linear-gradient(#f6f7f8,#e9ebee)}
.eyebrow{font-family:"Roboto",sans-serif;font-weight:400;letter-spacing:2px;text-transform:uppercase;color:var(--slate)}
.contact-name{font-family:"Poppins",sans-serif;font-weight:400;color:var(--navy)}
.rule{position:absolute;height:1px;background:var(--line)}
.contact-item{position:absolute;display:flex;align-items:center;font-family:"Roboto",sans-serif;color:#222}
.hours{position:absolute;font-family:"Roboto",sans-serif;font-weight:300;color:#777}
.map{position:absolute;background:linear-gradient(150deg,#4e5a3c,#2f3a2a 40%,#4c5848 70%,#6d7466)}
.map-card{position:absolute;background:var(--white);font-family:"Roboto",sans-serif;color:#222}
.map-card .link{color:#1a73e8}
.reviews{position:absolute;left:0;right:0;background:linear-gradient(#f1f2f4,#ffffff 40%)}
.reviews-title{font-family:"Poppins",sans-serif;font-weight:400;letter-spacing:1.5px;color:var(--slate);text-transform:uppercase}
.reviews-lead{font-family:"Roboto",sans-serif;font-weight:400;color:#2a3a55;line-height:1.2}
.review-card{position:absolute;background:var(--white);border:1px solid #e3e5e8;border-radius:3px;font-family:"Roboto",sans-serif}
.avatar{position:absolute;background:#c9a48a;border-radius:2px}
.reviewer{position:absolute;color:#333}
.company{position:absolute;color:#999}
.stars{position:absolute;color:var(--navy);letter-spacing:1px}
.quote{position:absolute;color:#888;font-weight:300;line-height:1.4}
.cta-band{position:absolute;left:0;right:0;background:var(--black)}
.cta-title{font-family:"Poppins",sans-serif;font-weight:500;color:var(--orange)}
.cta-text{font-family:"Roboto",sans-serif;font-weight:300;color:#444;line-height:1.35}
</style>
</head>
<body>

<div class="board-title">let me know if you need to adjust or revise this design</div>
<div class="view-label" style="left:223px">desktop view</div>
<div class="view-label" style="left:758px">mobile/tablet view</div>

<!-- ============ DESKTOP ============ -->
<main class="frame frame--desktop">

  <div class="admin-bar" style="height:16px">
    <span><i class="dot"></i>Sitebase</span><span>Customize</span><span>2</span><span>0</span><span>+ New</span><span>Edit Page</span><span>Edit with Builder</span><span>Notes</span><span class="spacer"></span><span>Howdy, admin</span>
  </div>

  <div class="hero-bg" style="top:16px;height:562px;clip-path:polygon(0 0,100% 0,100% 100%,0 90.2%)"></div>

  <header class="site-header" style="top:16px;height:62px">
    <div class="brand" style="left:40px;top:10px;width:70px;font-size:7px">
      <span class="mark" style="width:22px;height:22px"></span>
      <span>Steadwell</span>
    </div>
    <nav class="nav" style="left:283px;top:27px">
      <span class="active">Home</span><span>Services</span><span>About Us</span><span>Reviews</span><span>Contact Us</span>
    </nav>
  </header>

  <div class="photo-hero" role="img" aria-label="Photo of the company service van parked outside a warehouse" style="top:78px;height:320px"></div>
  <div class="social-rail" style="top:297px;width:34px;height:89px"><span style="width:10px;height:10px"></span><span style="width:10px;height:10px"></span><span style="width:10px;height:10px"></span></div>

  <p class="abs center hero-kicker" style="top:394px;font-size:12px">HVAC Solutions for Every Season</p>
  <h1 class="abs center hero-title" style="top:426px;font-size:23px">Your Comfort, Our Expertise</h1>
  <a class="btn btn--quote" style="left:230px;top:473px;width:140px;height:24px;font-size:8px">Get a Free Quote</a>

  <!-- Services -->
  <h2 class="abs center section-title" style="top:630px;font-size:30px">Our Services</h2>
  <p class="abs lead" style="top:672px;left:55px;width:490px;text-align:center;font-size:10.5px;line-height:16px">We’re <b>Steadwell</b>, your local HVAC experts serving Serving Charleston, SC, and Surrounding Areas since 2003. Our professional team is dedicated to keeping your home or business comfortable with top-quality service.</p>

  <div class="service-photo" role="img" aria-label="Technician repairing an outdoor heating unit" style="left:49px;top:762px;width:119px;height:79px"></div>
  <div class="service-photo alt" role="img" aria-label="Hand cleaning an outdoor unit with a cloth" style="left:176px;top:762px;width:120px;height:79px"></div>
  <div class="service-photo warm" role="img" aria-label="Technician servicing an AC condenser" style="left:304px;top:762px;width:120px;height:79px"></div>
  <div class="service-photo" role="img" aria-label="Technician maintaining an AC unit" style="left:432px;top:762px;width:120px;height:79px"></div>

  <h3 class="service-name" style="left:44px;width:130px;top:864px;font-size:10.5px">Heating Repair</h3>
  <h3 class="service-name" style="left:171px;width:130px;top:864px;font-size:10.5px">Heating Maintenance</h3>
  <h3 class="service-name" style="left:299px;width:130px;top:864px;font-size:10.5px">AC Repair</h3>
  <h3 class="service-name" style="left:427px;width:130px;top:864px;font-size:10.5px">AC Maintenance</h3>
  <p class="service-text" style="left:44px;width:130px;top:878px;font-size:7.8px">Our skilled technicians diagnose and address specific issues affecting the system.</p>
  <p class="service-text" style="left:171px;width:130px;top:878px;font-size:7.8px">We inspect various components, fine-tune system settings, and check for potential issues.</p>
  <p class="service-text" style="left:299px;width:130px;top:878px;font-size:7.8px">When repairing an AC system, our trained technicians start by diagnosing the issue.</p>
  <p class="service-text" style="left:427px;width:130px;top:878px;font-size:7.8px">Maintenance is essential for longevity and efficiency. We inspect and clean various components.</p>

  <a class="btn btn--book" style="left:251px;top:942px;width:99px;height:29px;font-size:13px">Book Now</a>

  <!-- Why us -->
  <section class="band-dark" style="top:981px;height:387px;clip-path:polygon(0 0,100% 14.2%,100% 100%,0 100%)"></section>
  <h2 class="abs center why-title" style="top:1097px;font-size:38px">Steadwell</h2>
  <p class="abs why-caps" style="top:1146px;left:50px;width:500px;text-align:center;font-size:7px">Experience unparalleled comfort with Steadwell Heating and Air’s premier air conditioning, heating, and plumbing services. Our commitment to excellence ensures your home is a haven of comfort, no matter the season.</p>

  <div class="feature" style="left:35px;width:120px;top:1197px">
    <svg width="30" height="32" viewBox="0 0 30 32"><path d="M4 0h7l4 8 4-8h7l-6 12" fill="none" stroke="#ee7325" stroke-width="3"/><circle cx="15" cy="21" r="9" fill="none" stroke="#ee7325" stroke-width="3"/><path d="M15 16l1.6 3.3 3.6.5-2.6 2.5.6 3.6-3.2-1.7-3.2 1.7.6-3.6-2.6-2.5 3.6-.5z" fill="#ee7325"/></svg>
    <h3 style="margin-top:27px;font-size:12.5px">Quality Service</h3>
    <p style="margin-top:4px;font-size:7px">Our experienced technicians are committed to delivering quality service and ensuring your HVAC system operates at its best.</p>
  </div>
  <div class="feature" style="left:172px;width:120px;top:1197px">
    <svg width="26" height="32" viewBox="0 0 26 32"><rect x="1.5" y="1.5" width="23" height="29" rx="2" fill="none" stroke="#ee7325" stroke-width="3"/><rect x="6" y="6" width="14" height="6" fill="#ee7325"/><g fill="#ee7325"><rect x="6" y="15" width="4" height="4"/><rect x="11" y="15" width="4" height="4"/><rect x="16" y="15" width="4" height="4"/><rect x="6" y="21" width="4" height="4"/><rect x="11" y="21" width="4" height="4"/><rect x="16" y="21" width="4" height="4"/></g></svg>
    <h3 style="margin-top:27px;font-size:12.5px">Affordability</h3>
    <p style="margin-top:4px;font-size:7px">We offer competitive pricing and transparent quotes to get your needed services without breaking the bank.</p>
  </div>
  <div class="feature" style="left:309px;width:120px;top:1197px">
    <svg width="32" height="32" viewBox="0 0 32 32"><path d="M16 2l4.2 8.6 9.4 1.4-6.8 6.6 1.6 9.4L16 23.6 7.6 28l1.6-9.4L2.4 12l9.4-1.4z" fill="none" stroke="#ee7325" stroke-width="3" stroke-linejoin="round"/></svg>
    <h3 style="margin-top:27px;font-size:12.5px">Customer<br>Satisfaction</h3>
    <p style="margin-top:4px;font-size:7px">Your satisfaction is our priority. We work diligently to exceed your expectations and provide personalized solutions.</p>
  </div>
  <div class="feature" style="left:446px;width:120px;top:1197px">
    <svg width="34" height="26" viewBox="0 0 34 26"><g fill="#ee7325"><circle cx="17" cy="7" r="5"/><circle cx="7" cy="9" r="3.5"/><circle cx="27" cy="9" r="3.5"/><path d="M8 24c0-6 4-9 9-9s9 3 9 9z"/><path d="M0 22c0-4 3-7 7-7 1.5 0 2.5.3 3.5 1-2 2-3 4-3 6z"/><path d="M34 22c0-4-3-7-7-7-1.5 0-2.5.3-3.5 1 2 2 3 4 3 6z"/></g></svg>
    <h3 style="margin-top:33px;font-size:12.5px">Community<br>Focus</h3>
    <p style="margin-top:4px;font-size:7px">We’re proud to serve Charleston and its surrounding islands. It is our way giving back to the community.</p>
  </div>

  <!-- Partners -->
  <section class="partners" style="top:1368px;height:185px"></section>
  <p class="abs center partners-label" style="top:1386px;font-size:10.5px">Major HVAC Equipment Brands We’re Partnered With</p>
  <div class="badge" role="img" aria-label="Partner brand badge" style="left:40px;top:1453px;width:20px;height:20px;border-radius:50%;background:#c8c8c8"></div>
  <div class="badge" role="img" aria-label="Partner brand badge" style="left:64px;top:1456px;width:62px;height:14px;border-radius:2px;background:#e2231a"></div>
  <div class="badge" role="img" aria-label="Partner brand badge" style="left:147px;top:1446px;width:95px;height:24px;border-radius:4px;background:#d71920"></div>
  <div class="badge" role="img" aria-label="Partner brand badge" style="left:252px;top:1448px;width:32px;height:32px;border-radius:50%;background:#e4281e"></div>
  <div class="badge" role="img" aria-label="Partner brand badge" style="left:290px;top:1456px;width:56px;height:14px;border-radius:2px;background:#e4281e"></div>
  <div class="badge" role="img" aria-label="Partner brand badge" style="left:361px;top:1436px;width:90px;height:54px;border-radius:12px;background:#3a3a3a"></div>
  <div class="badge" role="img" aria-label="Partner brand badge" style="left:481px;top:1434px;width:60px;height:60px;border-radius:50%;background:#e41b23"></div>

  <!-- Contact -->
  <section class="contact" style="top:1553px;height:310px"></section>
  <p class="abs eyebrow" style="left:12px;top:1589px;font-size:9px">Contact Us</p>
  <h2 class="abs contact-name" style="left:12px;top:1605px;font-size:19.5px">Steadwell Heating And Air</h2>
  <div class="rule" style="left:12px;top:1643px;width:232px"></div>
  <div class="contact-item" style="left:12px;top:1655px;font-size:9.5px"><svg width="14" height="10" viewBox="0 0 14 10" style="margin-right:12px"><rect x="1" y="1" width="12" height="8" fill="none" stroke="#1a2a3a" stroke-width="1.5"/><path d="M1 1l6 5 6-5" fill="none" stroke="#1a2a3a" stroke-width="1.5"/></svg>hello@steadwellhvac.com</div>
  <div class="contact-item" style="left:12px;top:1687px;font-size:9.5px"><svg width="14" height="12" viewBox="0 0 14 14" style="margin-right:12px"><path d="M3 1l3 3-2 2c1 2 2 3 4 4l2-2 3 3-2 2C6 13 1 8 1 3z" fill="#1a2a3a"/></svg>(843) 555-0142</div>
  <div class="contact-item" style="left:12px;top:1719px;font-size:9.5px"><svg width="14" height="11" viewBox="0 0 14 11" style="margin-right:12px"><rect x="1" y="1" width="12" height="9" fill="none" stroke="#1a2a3a" stroke-width="1.5"/><rect x="3" y="3.5" width="3" height="3" fill="#1a2a3a"/><path d="M8 4h3M8 7h3" stroke="#1a2a3a"/></svg>1480 Harbor Pine Avenue, Charleston, SC 29414</div>
  <div class="contact-item" style="left:12px;top:1751px;font-size:9.5px"><svg width="14" height="14" viewBox="0 0 14 14" style="margin-right:12px"><circle cx="7" cy="7" r="5.5" fill="none" stroke="#1a2a3a" stroke-width="1.5"/><path d="M7 4v3l2 2" fill="none" stroke="#1a2a3a" stroke-width="1.3"/></svg>Business Hours</div>
  <p class="hours" style="left:40px;top:1777px;font-size:7.5px">Mon – Fri &nbsp;&nbsp;7:00 am – 6:00 pm</p>
  <p class="hours" style="left:40px;top:1797px;font-size:7.5px">Saturday &nbsp;&nbsp;8:00 am – 3:00 pm</p>
  <p class="hours" style="left:40px;top:1817px;font-size:7.5px">Sunday &nbsp;&nbsp;&nbsp;Appointment Only</p>

  <div class="map" role="img" aria-label="Satellite map showing the office location" style="left:300px;top:1602px;width:297px;height:233px"></div>
  <div class="map-card" style="left:306px;top:1607px;width:150px;height:48px;padding:5px 6px;font-size:5.5px;line-height:1.4">
    <b>1480 Harbor Pine Avenue</b><br>1480 Harbor Pine Avenue,<br>Charleston, SC 29414, USA<br><span class="link">View larger map</span>
  </div>

  <!-- Reviews -->
  <section class="reviews" style="top:1863px;height:455px"></section>
  <h2 class="abs center reviews-title" style="top:1945px;font-size:16px">Our Happy Customers</h2>
  <p class="abs reviews-lead" style="left:110px;width:380px;top:1972px;text-align:center;font-size:8.3px">Explore The Firsthand Experiences Of Those Who Have Benefited Directly From Our Services. Our Reputation Is Built On A Foundation Of Unwavering Consistency, Exceptional Expertise, And Unwavering Commitment To Customer Support.</p>

  <article class="review-card" style="left:40px;top:2080px;width:158px;height:165px">
    <div class="avatar" role="img" aria-label="Customer portrait" style="left:16px;top:16px;width:18px;height:18px"></div>
    <p class="reviewer" style="left:0;right:0;top:45px;text-align:center;font-size:9.5px">Corin Jaye</p>
    <p class="company" style="left:0;right:0;top:60px;text-align:center;font-size:6.5px">Oakfield Lots, LLC</p>
    <p class="stars" style="left:16px;top:71px;font-size:7px">★★★★★</p>
    <p class="quote" style="left:16px;right:16px;top:84px;font-size:7px">“My move was way less stressful than expected! Swiftmove packed everything, stored it for a week, and moved it all to my new home just as promised!”</p>
  </article>
  <article class="review-card" style="left:221px;top:2080px;width:158px;height:165px">
    <div class="avatar" role="img" aria-label="Customer portrait" style="left:16px;top:16px;width:18px;height:18px;background:#9b6a4e"></div>
    <p class="reviewer" style="left:0;right:0;top:45px;text-align:center;font-size:9.5px">Elin Hart</p>
    <p class="company" style="left:0;right:0;top:60px;text-align:center;font-size:6.5px">Hartwell Legal Group</p>
    <p class="stars" style="left:16px;top:71px;font-size:7px">★★★★★</p>
    <p class="quote" style="left:16px;right:16px;top:84px;font-size:7px">“Swiftmove provided a very professional service when we moved offices last month. They were easy to work with and moved everything on time.”</p>
  </article>
  <article class="review-card" style="left:403px;top:2080px;width:158px;height:165px">
    <div class="avatar" role="img" aria-label="Customer portrait" style="left:16px;top:16px;width:18px;height:18px;background:#b98d74"></div>
    <p class="reviewer" style="left:0;right:0;top:45px;text-align:center;font-size:9.5px">Emmett Sayles</p>
    <p class="company" style="left:0;right:0;top:60px;text-align:center;font-size:6.5px">BrightCart</p>
    <p class="stars" style="left:16px;top:71px;font-size:7px">★★★★★</p>
    <p class="quote" style="left:16px;right:16px;top:84px;font-size:7px">Best experience ever! I desperately needed a mover to help with a last minute relocation, and Swiftmove was so helpful in making it a seamless process!”</p>
  </article>

  <!-- CTA -->
  <section class="cta-band" style="top:2318px;height:187px"></section>
  <h2 class="abs center cta-title" style="top:2348px;font-size:23px">Ready to Get Started?</h2>
  <p class="abs cta-text" style="left:135px;width:330px;top:2395px;text-align:center;font-size:7.3px">Experience unparalleled comfort with Steadwell Heating and Air’s premier Air Conditioning, Heating, and Plumbing services. Our commitment to excellence ensures your home is a haven of comfort, no matter the season.</p>
  <a class="btn btn--cta" style="left:251px;top:2455px;width:99px;height:30px;font-size:8.5px">Get A Quote</a>
</main>

<!-- ============ MOBILE / TABLET ============ -->
<main class="frame frame--mobile">

  <div class="admin-bar" style="height:13px;font-size:4.5px;gap:6px;padding:0 6px">
    <span><i class="dot" style="width:5px;height:5px"></i>Sitebase</span><span>Customize</span><span>2</span><span>0</span><span>+ New</span><span>Edit Page</span><span>Edit with Builder</span><span>Notes</span><span class="spacer"></span>
  </div>

  <div class="hero-bg" style="top:13px;height:422px;clip-path:polygon(0 0,100% 0,100% 100%,0 92.9%)"></div>

  <header class="site-header" style="top:13px;height:47px">
    <div class="brand" style="left:35px;top:8px;width:55px;font-size:5px;gap:2px">
      <span class="mark" style="width:16px;height:16px"></span>
      <span>Steadwell</span>
    </div>
    <p class="abs" style="right:40px;top:2px;font-size:4.5px;color:#c3c4c7">Howdy, admin</p>
    <svg class="abs" style="right:22px;top:17px" width="9" height="7" viewBox="0 0 9 7"><path d="M0 .5h9M0 3.5h9M0 6.5h9" stroke="#666" stroke-width="1"/></svg>
  </header>

  <div class="photo-hero" role="img" aria-label="Photo of the company service van parked outside a warehouse" style="top:60px;height:183px"></div>
  <div class="social-rail" style="top:186px;width:21px;height:67px"><span style="width:8px;height:8px"></span><span style="width:8px;height:8px"></span><span style="width:8px;height:8px"></span></div>

  <p class="abs center hero-kicker" style="top:258px;font-size:8px">HVAC Solutions for Every Season</p>
  <h1 class="abs center hero-title" style="top:273px;font-size:22px">Your Comfort,<br>Our Expertise</h1>
  <a class="btn btn--quote" style="left:114px;top:326px;width:118px;height:22px;font-size:6.5px">Get a Free Quote</a>

  <h2 class="abs center section-title" style="top:472px;font-size:17px">Our Services</h2>
  <p class="abs lead" style="top:495px;left:18px;width:309px;text-align:center;font-size:5.5px;line-height:9px">We’re <b>Steadwell</b>, your local HVAC experts serving Serving Charleston, SC, and Surrounding Areas since 2003. Our professional team is dedicated to keeping your home or business comfortable with top-quality service.</p>

  <div class="service-photo" role="img" aria-label="Technician repairing an outdoor heating unit" style="left:17px;top:545px;width:140px;height:94px"></div>
  <div class="service-photo alt" role="img" aria-label="Hand cleaning an outdoor unit with a cloth" style="left:188px;top:545px;width:140px;height:94px"></div>
  <div class="service-photo warm" role="img" aria-label="Technician servicing an AC condenser" style="left:17px;top:711px;width:140px;height:94px"></div>
  <div class="service-photo" role="img" aria-label="Technician maintaining an AC unit" style="left:188px;top:711px;width:140px;height:94px"></div>

  <h3 class="service-name" style="left:12px;width:150px;top:657px;font-size:8.5px">Heating Repair</h3>
  <h3 class="service-name" style="left:183px;width:150px;top:657px;font-size:8.5px">Heating Maintenance</h3>
  <p class="service-text" style="left:17px;width:140px;top:670px;font-size:5.5px">Our skilled technicians diagnose and address specific issues affecting the system.</p>
  <p class="service-text" style="left:188px;width:140px;top:670px;font-size:5.5px">We inspect various components, fine-tune system settings, and check for potential issues.</p>
  <h3 class="service-name" style="left:12px;width:150px;top:823px;font-size:8.5px">AC Repair</h3>
  <h3 class="service-name" style="left:183px;width:150px;top:823px;font-size:8.5px">AC Maintenance</h3>
  <p class="service-text" style="left:17px;width:140px;top:836px;font-size:5.5px">When repairing an AC system, our trained technicians start by diagnosing the issue.</p>
  <p class="service-text" style="left:188px;width:140px;top:836px;font-size:5.5px">Maintenance is essential for longevity and efficiency. We inspect and clean various components.</p>

  <a class="btn btn--book" style="left:143px;top:871px;width:59px;height:19px;font-size:5px">Book Now</a>

  <section class="band-dark" style="top:914px;height:307px;clip-path:polygon(0 0,100% 7.8%,100% 100%,0 100%)"></section>
  <h2 class="abs center why-title" style="top:977px;font-size:17px">Steadwell</h2>
  <p class="abs why-caps" style="top:1002px;left:15px;width:315px;text-align:center;font-size:5.5px">Experience unparalleled comfort with Steadwell Heating and Air’s premier air conditioning, heating, and plumbing services. Our commitment to excellence ensures your home is a haven of comfort, no matter the season.</p>

  <div class="feature" style="left:15px;width:70px;top:1050px">
    <svg width="20" height="22" viewBox="0 0 30 32"><path d="M4 0h7l4 8 4-8h7l-6 12" fill="none" stroke="#ee7325" stroke-width="3"/><circle cx="15" cy="21" r="9" fill="none" stroke="#ee7325" stroke-width="3"/><path d="M15 16l1.6 3.3 3.6.5-2.6 2.5.6 3.6-3.2-1.7-3.2 1.7.6-3.6-2.6-2.5 3.6-.5z" fill="#ee7325"/></svg>
    <h3 style="margin-top:30px;font-size:8px">Quality<br>Service</h3>
    <p style="margin-top:3px;font-size:5.2px">Our experienced technicians are committed to delivering quality service and ensuring your HVAC system operates at its best.</p>
  </div>
  <div class="feature" style="left:97px;width:70px;top:1050px">
    <svg width="17" height="22" viewBox="0 0 26 32"><rect x="1.5" y="1.5" width="23" height="29" rx="2" fill="none" stroke="#ee7325" stroke-width="3"/><rect x="6" y="6" width="14" height="6" fill="#ee7325"/><g fill="#ee7325"><rect x="6" y="15" width="4" height="4"/><rect x="11" y="15" width="4" height="4"/><rect x="16" y="15" width="4" height="4"/><rect x="6" y="21" width="4" height="4"/><rect x="11" y="21" width="4" height="4"/><rect x="16" y="21" width="4" height="4"/></g></svg>
    <h3 style="margin-top:30px;font-size:8px">Affordability</h3>
    <p style="margin-top:3px;font-size:5.2px">We offer competitive pricing and transparent quotes to get your needed services without breaking the bank.</p>
  </div>
  <div class="feature" style="left:179px;width:70px;top:1050px">
    <svg width="22" height="22" viewBox="0 0 32 32"><path d="M16 2l4.2 8.6 9.4 1.4-6.8 6.6 1.6 9.4L16 23.6 7.6 28l1.6-9.4L2.4 12l9.4-1.4z" fill="none" stroke="#ee7325" stroke-width="3" stroke-linejoin="round"/></svg>
    <h3 style="margin-top:30px;font-size:8px">Customer<br>Satisfaction</h3>
    <p style="margin-top:3px;font-size:5.2px">Your satisfaction is our priority. We work diligently to exceed your expectations and provide personalized solutions.</p>
  </div>
  <div class="feature" style="left:260px;width:70px;top:1050px">
    <svg width="26" height="20" viewBox="0 0 34 26"><g fill="#ee7325"><circle cx="17" cy="7" r="5"/><circle cx="7" cy="9" r="3.5"/><circle cx="27" cy="9" r="3.5"/><path d="M8 24c0-6 4-9 9-9s9 3 9 9z"/><path d="M0 22c0-4 3-7 7-7 1.5 0 2.5.3 3.5 1-2 2-3 4-3 6z"/><path d="M34 22c0-4-3-7-7-7-1.5 0-2.5.3-3.5 1 2 2 3 4 3 6z"/></g></svg>
    <h3 style="margin-top:32px;font-size:8px">Community<br>Focus</h3>
    <p style="margin-top:3px;font-size:5.2px">We’re proud to serve Charleston and its surrounding islands. It is our way giving back to the community .</p>
  </div>

  <section class="partners" style="top:1221px;height:345px;background:var(--white)"></section>
  <p class="abs center partners-label" style="top:1236px;font-size:5.5px">Major HVAC Equipment Brands We’re Partnered With</p>
  <div class="badge" role="img" aria-label="Partner brand badge" style="left:17px;top:1282px;width:12px;height:12px;border-radius:50%;background:#c8c8c8"></div>
  <div class="badge" role="img" aria-label="Partner brand badge" style="left:33px;top:1284px;width:36px;height:9px;border-radius:2px;background:#e2231a"></div>
  <div class="badge" role="img" aria-label="Partner brand badge" style="left:82px;top:1277px;width:53px;height:14px;border-radius:3px;background:#d71920"></div>
  <div class="badge" role="img" aria-label="Partner brand badge" style="left:144px;top:1279px;width:18px;height:18px;border-radius:50%;background:#e4281e"></div>
  <div class="badge" role="img" aria-label="Partner brand badge" style="left:166px;top:1284px;width:32px;height:9px;border-radius:2px;background:#e4281e"></div>
  <div class="badge" role="img" aria-label="Partner brand badge" style="left:210px;top:1272px;width:52px;height:31px;border-radius:8px;background:#3a3a3a"></div>
  <div class="badge" role="img" aria-label="Partner brand badge" style="left:275px;top:1262px;width:50px;height:50px;border-radius:50%;background:#e41b23"></div>

  <p class="abs eyebrow" style="left:14px;top:1346px;font-size:6px">Contact Us</p>
  <h2 class="abs contact-name" style="left:14px;top:1361px;font-size:12.5px">Steadwell Heating And Air</h2>
  <div class="rule" style="left:14px;top:1407px;width:293px"></div>
  <div class="contact-item" style="left:14px;top:1415px;font-size:6.5px"><svg width="11" height="8" viewBox="0 0 14 10" style="margin-right:11px"><rect x="1" y="1" width="12" height="8" fill="none" stroke="#1a2a3a" stroke-width="1.5"/><path d="M1 1l6 5 6-5" fill="none" stroke="#1a2a3a" stroke-width="1.5"/></svg>hello@steadwellhvac.com</div>
  <div class="contact-item" style="left:14px;top:1435px;font-size:6.5px"><svg width="11" height="10" viewBox="0 0 14 14" style="margin-right:11px"><path d="M3 1l3 3-2 2c1 2 2 3 4 4l2-2 3 3-2 2C6 13 1 8 1 3z" fill="#1a2a3a"/></svg>(843) 555-0142</div>
  <div class="contact-item" style="left:14px;top:1455px;font-size:6.5px"><svg width="11" height="9" viewBox="0 0 14 11" style="margin-right:11px"><rect x="1" y="1" width="12" height="9" fill="none" stroke="#1a2a3a" stroke-width="1.5"/><rect x="3" y="3.5" width="3" height="3" fill="#1a2a3a"/><path d="M8 4h3M8 7h3" stroke="#1a2a3a"/></svg>1480 Harbor Pine Avenue, Charleston, SC 29414</div>
  <div class="contact-item" style="left:14px;top:1475px;font-size:6.5px"><svg width="11" height="11" viewBox="0 0 14 14" style="margin-right:11px"><circle cx="7" cy="7" r="5.5" fill="none" stroke="#1a2a3a" stroke-width="1.5"/><path d="M7 4v3l2 2" fill="none" stroke="#1a2a3a" stroke-width="1.3"/></svg>Business Hours</div>
  <p class="hours" style="left:14px;top:1497px;font-size:5.5px">Mon – Fri &nbsp;&nbsp;7:00 am – 6:00 pm</p>
  <p class="hours" style="left:14px;top:1513px;font-size:5.5px">Saturday &nbsp;&nbsp;8:00 am – 3:00 pm</p>
  <p class="hours" style="left:14px;top:1529px;font-size:5.5px">Sunday &nbsp;&nbsp;&nbsp;Appointment Only</p>

  <div class="map" role="img" aria-label="Satellite map showing the office location" style="left:0;top:1566px;width:340px;height:270px"></div>
  <div class="map-card" style="left:4px;top:1570px;width:125px;height:42px;padding:4px 5px;font-size:4.5px;line-height:1.4">
    <b>1480 Harbor Pine Avenue</b><br>1480 Harbor Pine Avenue,<br>Charleston, SC 29414, USA<br><span class="link">View larger map</span>
  </div>

  <section class="reviews" style="top:1836px;height:364px"></section>
  <h2 class="abs center reviews-title" style="top:1903px;font-size:11px;letter-spacing:.5px">Our Happy Customers</h2>
  <p class="abs reviews-lead" style="left:52px;width:240px;top:1917px;text-align:center;font-size:6.8px">Explore The Firsthand Experiences Of Those Who Have Benefited Directly From Our Services. Our Reputation Is Built On A Foundation Of Unwavering Consistency, Exceptional Expertise, And Unwavering Commitment To Customer Support.</p>

  <article class="review-card" style="left:15px;top:1978px;width:98px;height:168px">
    <div class="avatar" role="img" aria-label="Customer portrait" style="left:10px;top:10px;width:22px;height:22px"></div>
    <p class="reviewer" style="left:35px;top:32px;font-size:6.5px;line-height:1.1">Corin<br>Jaye</p>
    <p class="company" style="left:35px;top:53px;font-size:4.5px">Oakfield Lots, LLC</p>
    <p class="stars" style="left:10px;top:72px;font-size:5.5px">★★★★★</p>
    <p class="quote" style="left:10px;right:8px;top:86px;font-size:5.2px">“My move was way less stressful than expected! Swiftmove packed everything, stored it for a week, and moved it all to my new home just as promised!”</p>
  </article>
  <article class="review-card" style="left:125px;top:1978px;width:98px;height:168px">
    <div class="avatar" role="img" aria-label="Customer portrait" style="left:10px;top:10px;width:22px;height:22px;background:#9b6a4e"></div>
    <p class="reviewer" style="left:35px;top:32px;font-size:6.5px">Elin Hart</p>
    <p class="company" style="left:35px;top:45px;font-size:4.5px;line-height:1.3">Hartwell Legal<br>Group</p>
    <p class="stars" style="left:10px;top:72px;font-size:5.5px">★★★★★</p>
    <p class="quote" style="left:10px;right:8px;top:86px;font-size:5.2px">“Swiftmove provided a very professional service when we moved offices last month. They were easy to work with and moved everything on time.”</p>
  </article>
  <article class="review-card" style="left:233px;top:1978px;width:98px;height:168px">
    <div class="avatar" role="img" aria-label="Customer portrait" style="left:10px;top:10px;width:22px;height:22px;background:#b98d74"></div>
    <p class="reviewer" style="left:35px;top:32px;font-size:6.5px;line-height:1.1">Emmett<br>Sayles</p>
    <p class="company" style="left:35px;top:53px;font-size:4.5px">BrightCart</p>
    <p class="stars" style="left:10px;top:72px;font-size:5.5px">★★★★★</p>
    <p class="quote" style="left:10px;right:8px;top:86px;font-size:5.2px">Best experience ever! I desperately needed a mover to help with a last minute relocation, and Swiftmove was so helpful in making it a seamless process!”</p>
  </article>

  <section class="cta-band" style="top:2200px;height:163px"></section>
  <h2 class="abs center cta-title" style="top:2229px;font-size:15px">Ready to Get Started?</h2>
  <p class="abs cta-text" style="left:60px;width:225px;top:2262px;text-align:center;font-size:5.3px">Experience unparalleled comfort with Steadwell Heating and Air’s premier Air Conditioning, Heating, and Plumbing services. Our commitment to excellence ensures your home is a haven of comfort, no matter the season.</p>
  <a class="btn btn--cta" style="left:131px;top:2314px;width:85px;height:26px;font-size:6.5px">Get A Quote</a>
</main>

</body>
</html>
```